sydney wedding photography business needs a business card design

we need a business card design for a sydney based wedding photography and videography business. our business name is :golden hour studio and film. our target clients are 24-35 yrs female. our style is candid, organic, natural, dynamic. we are a team of young photographers and videographers, and help brides to create memories that they will cherish for the rest of their lives. the logo will be provided. we want an elegant design that reflects our style, and also want to give a great impression to our clients that we are one of the best studios in sydney and our brand means quality and premium service.

Target Market(s)

bride to be, 24-35 years old, living in sydney and surrunding areas

Industry/Entity Type

Wedding Photography

Contact Information for Business Card

address: 57 tarrant street, glenmore nsw 2047
mobile: 0431872259
phone: (02) 9163 2408
info@tidewillowstudio.net.au
www.tidewillowstudio.net.au
facebook:tidewillowweddings
instagram:tidewillowweddings

Font styles to use
Serif
Sans Serif

Requirements
Nice to have
• maybe add my slogan"memories beyond eternity" if the layout looks good
Should not have
• no black color, not good idea for wedding biz card

```html
<!DOCTYPE html>
<html lang="en">
<head>
<meta charset="utf-8">
<title>Golden Hour Studio and Film – Business Card</title>
<link rel="stylesheet" href="https://fonts.googleapis.com/css2?family=Jost:wght@300;400;500&display=swap">
<style>
  :root {
    --backdrop: #e9e4da;
    --gold-light: #e6b52c;
    --gold: #c9951a;
    --gold-deep: #a87a10;
    --espresso: #3a2a1a;
    --espresso-deep: #24180e;
    --silver: #e4e0d8;
    --text-dark: #2e2114;
    --text-light: #f6f1e6;
  }
  html, body {
    margin: 0;
    width: 1200px;
    height: 950px;
    overflow: hidden;
    background: var(--backdrop);
    font-family: "Jost", sans-serif;
  }
  .sheet {
    width: 1200px;
    height: 950px;
    display: flex;
    flex-direction: column;
    align-items: center;
    justify-content: center;
    gap: 50px;
  }
  .card {
    position: relative;
    width: 700px;
    height: 400px;
    box-shadow: 0 10px 30px rgba(0,0,0,0.22);
    overflow: hidden;
  }
  .card-art { position: absolute; inset: 0; }
  .card-back {
    background: linear-gradient(135deg, var(--gold-light), var(--gold) 55%, var(--gold-deep));
  }
  .holder {
    position: absolute;
    top: 28px;
    right: 150px;
    text-align: right;
    color: var(--text-dark);
    line-height: 1;
  }
  .holder-name { font-size: 26px; font-weight: 400; letter-spacing: 1px; }
  .holder-role { font-size: 12px; font-weight: 400; letter-spacing: 1.5px; margin-top: 4px; }
  .contact {
    position: absolute;
    left: 290px;
    top: 225px;
    color: var(--text-light);
    font-size: 14px;
    font-weight: 300;
    line-height: 1.3;
  }
  .contact-address { margin: 0 0 6px; }
  .contact-list { list-style: none; margin: 0; padding: 0; }
  .contact-list li { display: flex; align-items: center; gap: 10px; }
  .contact-icon { width: 12px; height: 12px; flex: none; }
  .brand {
    position: absolute;
    right: 50px;
    top: 150px;
    text-align: center;
    color: var(--gold-light);
    font-weight: 500;
    line-height: 1.1;
  }
  .brand-main { font-size: 36px; }
  .brand-sub { font-size: 13px; letter-spacing: 5px; text-transform: uppercase; }
</style>
</head>
<body>
<main class="sheet">
  <section class="card card-front" aria-label="Business card front">
    <svg class="card-art" viewBox="0 0 700 400" aria-hidden="true">
      <defs>
        <linearGradient id="goldFill" x1="0" y1="0" x2="1" y2="1">
          <stop offset="0" stop-color="#e6b52c"/>
          <stop offset="0.6" stop-color="#c9951a"/>
          <stop offset="1" stop-color="#a87a10"/>
        </linearGradient>
        <linearGradient id="espressoFill" x1="0" y1="0" x2="1" y2="1">
          <stop offset="0" stop-color="#3a2a1a"/>
          <stop offset="1" stop-color="#24180e"/>
        </linearGradient>
      </defs>
      <rect class="card-ground" width="700" height="400" fill="url(#goldFill)"/>
      <path class="swoosh-line" d="M250,140 C380,95 520,85 700,20 L700,40 C530,100 390,110 250,140 Z" fill="#3a2a1a"/>
      <path class="swoosh-silver" d="M95,400 C140,250 240,170 420,140 C280,185 180,260 130,400 Z" fill="#e4e0d8"/>
      <path class="panel-espresso" d="M120,400 C170,250 300,170 470,140 C590,118 650,90 700,60 L700,400 Z" fill="url(#espressoFill)"/>
    </svg>

    <div class="holder">
      <div class="holder-name">LIAM HARPER</div>
      <div class="holder-role">PHOTOGRAPHER</div>
    </div>

    <div class="contact">
      <p class="contact-address">57 tarrant street<br>glenmore nsw 2047</p>
      <ul class="contact-list">
        <li>
          <svg class="contact-icon" viewBox="0 0 12 12"><path d="M2.5 1 L4.5 1 L5.3 3.6 L4 4.6 C4.7 6 6 7.3 7.4 8 L8.4 6.7 L11 7.5 L11 9.5 C11 10.3 10.3 11 9.5 11 C5 11 1 7 1 2.5 C1 1.7 1.7 1 2.5 1 Z" fill="#e6b52c"/></svg>
          (02) 9163 2408
        </li>
        <li>
          <svg class="contact-icon" viewBox="0 0 12 12"><rect x="3" y="0.5" width="6" height="11" rx="1.2" fill="none" stroke="#e6b52c" stroke-width="1.3"/></svg>
          0431 872 259
        </li>
        <li>
          <svg class="contact-icon" viewBox="0 0 12 12"><rect x="0.5" y="2" width="11" height="8" fill="none" stroke="#e6b52c" stroke-width="1.2"/><path d="M0.5 2 L6 7 L11.5 2" fill="none" stroke="#e6b52c" stroke-width="1.2"/></svg>
          info@tidewillowstudio.net.au
        </li>
        <li>
          <svg class="contact-icon" viewBox="0 0 12 12"><circle cx="6" cy="6" r="5.3" fill="none" stroke="#e6b52c" stroke-width="1.2"/><path d="M0.7 6 H11.3 M6 0.7 C3.5 3.5 3.5 8.5 6 11.3 M6 0.7 C8.5 3.5 8.5 8.5 6 11.3" fill="none" stroke="#e6b52c" stroke-width="1"/></svg>
          www.tidewillowstudio.net.au
        </li>
        <li>
          <svg class="contact-icon" viewBox="0 0 12 12"><rect x="1" y="1" width="10" height="10" fill="#e6b52c"/></svg>
          tidewillowweddings
        </li>
        <li>
          <svg class="contact-icon" viewBox="0 0 12 12"><rect x="1" y="1" width="10" height="10" fill="#e6b52c"/></svg>
          tidewillowweddings
        </li>
      </ul>
    </div>

    <div class="brand">
      <div class="brand-main">Golden Hour</div>
      <div class="brand-sub">studio and film</div>
    </div>
  </section>

  <section class="card card-back" aria-label="Business card back"></section>
</main>
</body>
</html>
```